Vantiqo custom business card design

Need a authentic, innovative business card design for a new mobile app business. I am uploading a few screen images from our app for you to view. I would like app design theme to match business card design. I can also send logo images.

```html
<!DOCTYPE html>
<html lang="en">
<head>
<meta charset="utf-8">
<title>Vantiqo Business Card</title>
<link rel="stylesheet" href="https://fonts.googleapis.com/css2?family=Open+Sans:wght@400;600;700;800&display=swap">
<style>
  :root {
    --stage: #2c2c2f;
    --brand-purple: #5e0a8c;
    --brand-purple-deep: #4d0675;
    --ink: #2a2a2a;
    --ink-soft: #3d3d3d;
    --paper: #ffffff;
    --paper-shade: #eeeeee;
    --divider: #b9b9b9;
  }
  * { box-sizing: border-box; margin: 0; padding: 0; }
  html, body {
    width: 1200px;
    height: 1000px;
    overflow: hidden;
    background: var(--stage);
    font-family: "Open Sans", Arial, sans-serif;
  }
  .stage {
    position: relative;
    width: 1200px;
    height: 1000px;
  }
  .card {
    position: absolute;
    left: 220px;
    width: 760px;
    height: 434px;
    border-radius: 22px;
    overflow: hidden;
  }

  /* Back of card */
  .card-back {
    top: 40px;
    background: linear-gradient(135deg, var(--brand-purple) 0%, var(--brand-purple-deep) 100%);
    display: flex;
    flex-direction: column;
    align-items: center;
    justify-content: center;
  }
  .back-brand {
    display: flex;
    align-items: center;
    gap: 22px;
  }
  .back-brand .brand-dot {
    width: 64px;
    height: 64px;
    border-radius: 50%;
    background: var(--paper);
  }
  .back-brand .brand-name {
    font-size: 64px;
    font-weight: 800;
    color: var(--paper);
    letter-spacing: -1px;
  }
  .back-web {
    margin-top: 40px;
    font-size: 20px;
    letter-spacing: 8px;
    color: var(--paper);
  }

  /* Front of card */
  .card-front {
    top: 526px;
    background: linear-gradient(160deg, var(--paper) 55%, var(--paper-shade) 100%);
    border-bottom: 14px solid var(--brand-purple);
    display: flex;
    align-items: center;
  }
  .front-brand {
    width: 330px;
    display: flex;
    flex-direction: column;
    align-items: center;
    gap: 18px;
  }
  .front-brand .brand-dot {
    width: 130px;
    height: 130px;
    border-radius: 50%;
    background: var(--brand-purple);
  }
  .front-brand .brand-name {
    font-size: 50px;
    font-weight: 800;
    color: var(--ink);
    letter-spacing: -1px;
  }
  .front-divider {
    width: 2px;
    height: 260px;
    background: linear-gradient(to bottom, transparent, var(--divider) 20%, var(--divider) 80%, transparent);
  }
  .contact {
    padding-left: 44px;
    color: var(--ink-soft);
  }
  .contact-name {
    font-size: 28px;
    font-weight: 800;
    color: var(--brand-purple);
    line-height: 1.1;
  }
  .contact-role {
    font-size: 19px;
    letter-spacing: 0.5px;
    margin-bottom: 12px;
  }
  .contact-address {
    font-size: 18px;
    line-height: 1.3;
    margin-bottom: 10px;
  }
  .contact-list { list-style: none; }
  .contact-list li {
    display: flex;
    align-items: center;
    gap: 14px;
    font-size: 19px;
    line-height: 1.45;
  }
  .contact-list svg {
    width: 18px;
    height: 18px;
    fill: var(--brand-purple);
    flex: none;
  }
</style>
</head>
<body>
<main class="stage">

  <section class="card card-back" aria-label="Card back">
    <div class="back-brand">
      <span class="brand-dot"></span>
      <span class="brand-name">Vantiqo</span>
    </div>
    <p class="back-web">www.vantiqo.com</p>
  </section>

  <section class="card card-front" aria-label="Card front">
    <div class="front-brand">
      <span class="brand-dot"></span>
      <span class="brand-name">Vantiqo</span>
    </div>
    <div class="front-divider"></div>
    <div class="contact">
      <h1 class="contact-name">MARCUS ELLERY</h1>
      <p class="contact-role">PRESIDENT</p>
      <p class="contact-address">2417 Harrow Lane<br>Maple Ridge, NY 11920</p>
      <ul class="contact-list">
        <li>
          <svg viewBox="0 0 20 20" aria-hidden="true"><path d="M2 7c0-3 4-4 8-4s8 1 8 4v1h-4V6.5c-1-.5-2.5-.7-4-.7s-3 .2-4 .7V8H2z"/><path d="M5 9h10l2 8H3z"/><circle cx="10" cy="13" r="2" fill="#fff"/></svg>
          <span>555 0142 7781</span>
        </li>
        <li>
          <svg viewBox="0 0 20 20" aria-hidden="true"><path d="M6 1h8a1.5 1.5 0 0 1 1.5 1.5v15A1.5 1.5 0 0 1 14 19H6a1.5 1.5 0 0 1-1.5-1.5v-15A1.5 1.5 0 0 1 6 1zm.5 3v11h7V4z"/></svg>
          <span>555 0198 3304</span>
        </li>
        <li>
          <svg viewBox="0 0 20 20" aria-hidden="true"><path d="M6 1h8v5H6z"/><path d="M2 7h16v9h-3v3H5v-3H2zm5 7v3h6v-3z"/></svg>
          <span>555 0167 2259</span>
        </li>
        <li>
          <svg viewBox="0 0 20 20" aria-hidden="true"><path d="M1 4h18v12H1z"/><path d="M1 4l9 7 9-7" fill="none" stroke="#fff" stroke-width="1.6"/></svg>
          <span>marcus@vantiqo.com</span>
        </li>
        <li>
          <svg viewBox="0 0 20 20" aria-hidden="true"><circle cx="10" cy="10" r="9"/><path d="M1 10h18M10 1c3 3 3 15 0 18M10 1c-3 3-3 15 0 18" fill="none" stroke="#fff" stroke-width="1.2"/></svg>
          <span>www.vantiqo.com</span>
        </li>
      </ul>
    </div>
  </section>

</main>
</body>
</html>
```